Medical Practice needs a Letterhead Design

We need a clean, modern letterhead design for our stem cell medical practice.

Industry/Entity Type

Medical

```html
<!DOCTYPE html>
<html lang="en">
<head>
<meta charset="utf-8">
<title>VitaCore Medical Letterhead</title>
<link rel="stylesheet" href="https://fonts.googleapis.com/css2?family=Open+Sans:wght@400;600&family=Poppins:wght@400&display=swap">
<style>
  :root {
    --stage: #a8a8a8;
    --paper: #ffffff;
    --navy: #12344a;
    --navy-soft: #1d4a63;
    --lime: #b5c935;
    --ink: #1f1f1f;
    --muted: #4a4a4a;
  }
  * { box-sizing: border-box; margin: 0; padding: 0; }
  html, body { width: 1200px; height: 1000px; overflow: hidden; }
  body { background: var(--stage); position: relative; font-family: "Open Sans", sans-serif; }

  .letterhead {
    position: absolute; left: 280px; top: 50px;
    width: 640px; height: 900px;
    background: var(--paper);
    box-shadow: 4px 6px 14px rgba(0,0,0,0.25);
    overflow: hidden;
  }
  .header-band {
    position: absolute; left: 0; top: 0; width: 640px; height: 84px;
    background: linear-gradient(180deg, var(--navy) 0%, var(--navy) 70%, var(--navy-soft) 100%);
  }

  .brand {
    position: absolute; right: 64px; top: 104px;
    color: var(--navy); font-weight: 400; text-align: center; line-height: 1;
  }
  .brand-name { font-size: 32px; letter-spacing: -0.5px; }
  .brand-sub { font-size: 10px; letter-spacing: 5px; margin-top: 4px; }

  .letter-body {
    position: absolute; left: 64px; top: 162px; width: 520px;
    font-size: 11.5px; line-height: 21px; color: var(--ink);
  }
  .salutation { margin-bottom: 22px; }
  .letter-body p.para { margin-bottom: 20px; }

  .sign-off { position: absolute; left: 64px; top: 630px; font-size: 11.5px; color: var(--ink); }
  .signature {
    width: 130px; height: 40px; margin: 8px 0 8px;
    background: linear-gradient(90deg, rgba(30,30,30,0.12), rgba(30,30,30,0.04));
    border-radius: 4px;
  }

  .contact-footer {
    position: absolute; left: 0; right: 0; top: 784px;
    font-family: "Poppins", sans-serif; font-size: 9px; color: var(--muted);
    text-align: center; line-height: 18px;
  }
  .contact-row { display: flex; justify-content: center; gap: 14px; }
  .contact-item { display: inline-flex; align-items: center; gap: 4px; }
  .contact-icon { width: 10px; height: 10px; }

  .footer-line { position: absolute; left: 0; right: 0; top: 838px; height: 5px; background: var(--lime); }
  .footer-band { position: absolute; left: 0; right: 0; top: 846px; bottom: 0; background: var(--navy); }
</style>
</head>
<body>
  <main class="letterhead">
    <div class="header-band" role="img" aria-label="Decorative navy and lime header wave"></div>

    <div class="brand">
      <div class="brand-name">VitaCore</div>
      <div class="brand-sub">MEDICAL</div>
    </div>

    <section class="letter-body">
      <p class="salutation">Lorem Ipsum is simply</p>
      <p class="para">dummy text of the printing and typesetting industry. Lorem Ipsum has been the industry's standard dummy text ever since the 1500s, when an unknown printer took a galley of type and scrambled it to make a type specimen book. It has survived not only five centuries, but also the leap into electronic typesetting, remaining essentially unchanged. It was popularised in the 1960s with the release of Typeset sheets containing Lorem Ipsum passages, and more recently with desktop publishing software like PageComposer including versions of Lorem Ipsum.</p>
      <p class="para">It is a long established fact that a reader will be distracted by the readable content of a page when looking at its layout. The point of using Lorem Ipsum is that it has a more-or-less normal distribution of letters, as opposed to using 'Content here, content here', making it look like readable English. Many desktop publishing packages and web page editors now use Lorem Ipsum as their default model text, and a search for 'lorem ipsum' will uncover many web sites still in their infancy. Various versions have evolved over the years, sometimes by accident, sometimes on purpose (injected humour and the like).</p>
      <p class="para">Contrary to popular belief, Lorem Ipsum is not simply random text. It has roots in a piece of classical Latin literature from 45 BC, making it over 2000 years old. Daniel Marlowe, a Latin professor at Ashford College</p>
    </section>

    <div class="sign-off">
      <p>Lorem Ipsum</p>
      <div class="signature" role="img" aria-label="Handwritten signature"></div>
      <p>Lorem Ipsum is a dummy</p>
    </div>

    <footer class="contact-footer">
      <div class="contact-row">
        <span class="contact-item">
          <svg class="contact-icon" viewBox="0 0 10 10" aria-hidden="true"><circle cx="5" cy="5" r="5" fill="var(--navy)"/><path d="M3.3 2.6 L4.3 3.8 L3.8 4.4 C4.2 5.2 4.8 5.8 5.6 6.2 L6.2 5.7 L7.4 6.7 L6.8 7.6 C4.8 7.4 2.6 5.2 2.4 3.2 Z" fill="#fff"/></svg>
          (000)412-3390
        </span>
        <span class="contact-item">
          <svg class="contact-icon" viewBox="0 0 10 10" aria-hidden="true"><circle cx="5" cy="5" r="5" fill="var(--navy)"/><rect x="2.5" y="3.5" width="5" height="3.5" fill="#fff"/><rect x="3.5" y="2.3" width="3" height="1.6" fill="#fff"/></svg>
          (000)412-3391
        </span>
        <span class="contact-item">
          <svg class="contact-icon" viewBox="0 0 10 10" aria-hidden="true"><circle cx="5" cy="5" r="5" fill="var(--navy)"/><rect x="2.4" y="3.2" width="5.2" height="3.6" fill="#fff"/><path d="M2.4 3.2 L5 5.2 L7.6 3.2" stroke="var(--navy)" stroke-width="0.6" fill="none"/></svg>
          hello@vitacoremed.com
        </span>
      </div>
      <div class="contact-row">
        <span class="contact-item">
          <svg class="contact-icon" viewBox="0 0 10 10" aria-hidden="true"><circle cx="5" cy="5" r="5" fill="var(--navy)"/><path d="M5 2 C3.6 2 2.8 3 2.8 4.1 C2.8 5.6 5 8 5 8 C5 8 7.2 5.6 7.2 4.1 C7.2 3 6.4 2 5 2 Z" fill="#fff"/><circle cx="5" cy="4.1" r="0.8" fill="var(--navy)"/></svg>
          48 Orchard Lane, Suite 210, Fairview, ST 40110
        </span>
      </div>
      <div class="contact-row">
        <span class="contact-item">
          <svg class="contact-icon" viewBox="0 0 10 10" aria-hidden="true"><circle cx="5" cy="5" r="5" fill="var(--navy)"/><circle cx="5" cy="5" r="2.6" fill="none" stroke="#fff" stroke-width="0.7"/><path d="M2.4 5 H7.6 M5 2.4 V7.6" stroke="#fff" stroke-width="0.6"/></svg>
          www.vitacoremed.com
        </span>
      </div>
    </footer>

    <div class="footer-line"></div>
    <div class="footer-band"></div>
  </main>
</body>
</html>
```